Leadership training for women Business + Spirit

I need a flyer for a leadership training to hand out after I've been doing public speaking. I would also like to send it as a PDF. so maybe A4 is a good size. I will probably also need a brochure, with some more in depth information, but to start with I like to just give them something so they get inspired to contact me for more information. You can see more of my style on www.brightmeadow.se . Its a training that combines business with spirit, heart with intellect. We focus both on strict leadership skills such as Setting objectives aligned with strategy, assess performance and spiritual practices such as meditation, connecting with your unique essence. I like the deign to communicate business and professional together with warmth, life and joy. Colourful with style. Empowerment. The attached style guide does not have to be followed strictly but please use it in combination with my site www.brightmeadow.se I've the logo in many different sizes. I've added the smallest one below. Use any images that you think might fit, doesn't have to be from my website, it could be from your resources. I've added some other images here in the brief too, I have many more but can't attach all of it :-).
Target Market(s)
Women in leadership positions age 30 - 60
Industry/Entity Type
Leadership
Look and feel

```html
<!DOCTYPE html>
<html lang="sv">
<head>
<meta charset="utf-8">
<title>Bright Meadow – Flyer</title>
<link rel="stylesheet" href="https://fonts.googleapis.com/css2?family=Oswald:wght@500;600&family=Lato:wght@300;400;700&display=swap">
<style>
  :root {
    --navy: #1c2f4b;
    --orange: #ee8a1f;
    --orange-deep: #e57d12;
    --white: #ffffff;
    --paper: #eff0f4;
    --ink: #1a1a1a;
    --backdrop: #2f2b28;
  }
  * { margin: 0; padding: 0; box-sizing: border-box; }
  html, body { width: 1200px; height: 1200px; overflow: hidden; background: var(--backdrop); }
  .canvas { position: relative; width: 1200px; height: 1200px; }
  .flyer {
    position: absolute; left: 194px; top: 30px;
    width: 860px; height: 1207px;
    transform: scale(0.944); transform-origin: top left;
    background: var(--paper); overflow: hidden;
    font-family: 'Lato', sans-serif;
  }
  .hero-photo {
    position: absolute; left: 0; top: 0; width: 860px; height: 580px;
    background:
      linear-gradient(160deg, #f0962a 0%, #e6902e 28%, rgba(200,140,90,0) 45%),
      linear-gradient(180deg, #d9a06a 0%, #c9a894 35%, #a58876 60%, #5b4034 85%, #3d2a22 100%);
  }
  .team-photo {
    position: absolute; left: 0; top: 790px; width: 860px; height: 382px;
    background:
      linear-gradient(90deg, rgba(60,60,80,.25) 8%, rgba(240,240,244,0) 20%, rgba(240,240,244,0) 80%, rgba(150,70,60,.25) 92%, rgba(240,240,244,0) 96%),
      linear-gradient(180deg, #eceef2 0%, #b9bccb 35%, #5d6788 60%, #d8d9de 92%, #e9eaee 100%);
  }
  .shapes { position: absolute; left: 0; top: 0; }
  .brand { position: absolute; left: 43px; top: 267px; display: flex; align-items: center; gap: 10px; }
  .brand-dot { width: 80px; height: 80px; border-radius: 50%; border: 2px solid var(--white); }
  .brand-name { font-weight: 300; font-size: 46px; color: var(--white); letter-spacing: -0.5px; }
  .headline {
    position: absolute; left: 26px; top: 376px;
    font-family: 'Oswald', sans-serif; font-weight: 600; font-size: 47px;
    line-height: 60px; color: var(--white); letter-spacing: -0.6px; text-transform: uppercase;
  }
  .pillars {
    position: absolute; left: 28px; top: 508px;
    font-family: 'Oswald', sans-serif; font-weight: 500; font-size: 23.5px; color: var(--white);
    letter-spacing: -0.2px;
  }
  .pillars span { margin: 0 6px; }
  .features-title {
    position: absolute; left: 517px; top: 398px;
    font-family: 'Oswald', sans-serif; font-weight: 500; font-size: 53px; line-height: 70px;
    color: var(--white); letter-spacing: -0.5px;
  }
  .features-rule { position: absolute; left: 477px; top: 468px; width: 361px; height: 3px; background: var(--white); }
  .features-list { position: absolute; left: 504px; top: 492px; list-style: none; }
  .features-list li {
    display: flex; align-items: center; gap: 10px; height: 53px;
    font-weight: 700; font-size: 25.5px; color: var(--white);
  }
  .features-list svg { width: 20px; height: 20px; flex: none; }
  .about-title {
    position: absolute; left: 27px; top: 616px;
    font-family: 'Oswald', sans-serif; font-weight: 500; font-size: 27px; color: var(--navy);
    letter-spacing: -0.5px;
  }
  .about-rule { position: absolute; left: 26px; top: 650px; width: 63px; height: 5px; background: var(--orange); }
  .about-text {
    position: absolute; left: 28px; top: 664px; width: 328px;
    font-size: 13px; line-height: 15.2px; color: var(--ink); text-align: justify;
  }
  .footer {
    position: absolute; left: 0; top: 1172px; width: 860px; height: 35px; background: var(--navy);
    display: flex; align-items: center; justify-content: center; gap: 12px;
    color: var(--white); font-size: 19px; letter-spacing: 0.6px;
  }
  .footer-dot { width: 11px; height: 11px; border-radius: 50%; background: var(--orange); }
</style>
</head>
<body>
<div class="canvas">
  <div class="flyer">
    <div class="hero-photo" role="img" aria-label="Woman standing with open arms on a mountain top above misty ranges at sunset"></div>
    <div class="team-photo" role="img" aria-label="Group of smiling women of different ages standing together in a bright room"></div>

    <svg class="shapes" width="860" height="1207" viewBox="0 0 860 1207" aria-hidden="true">
      <path fill="var(--navy)" d="M0,270 C100,195 270,195 400,250 C480,285 550,340 610,400 L610,720 L450,690 C330,620 150,590 0,609 Z"/>
      <circle cx="642" cy="582" r="229" fill="var(--orange-deep)"/>
    </svg>

    <div class="brand">
      <div class="brand-dot"></div>
      <div class="brand-name">Bright Meadow</div>
    </div>

    <h1 class="headline">Business med hjärta,<br>själ med intellekt</h1>
    <p class="pillars">LEDARSKAP<span>|</span>VARANDET<span>|</span>EMPOWERMENT</p>

    <h2 class="features-title">KEY FEATURES</h2>
    <div class="features-rule"></div>
    <ul class="features-list">
      <li><svg viewBox="0 0 20 20"><rect x="1.5" y="4" width="14" height="14" fill="none" stroke="#fff" stroke-width="2"/><path d="M5 10 L9 14 L18 2" fill="none" stroke="#fff" stroke-width="3"/></svg>Sätta mål &amp; delegera</li>
      <li><svg viewBox="0 0 20 20"><rect x="1.5" y="4" width="14" height="14" fill="none" stroke="#fff" stroke-width="2"/><path d="M5 10 L9 14 L18 2" fill="none" stroke="#fff" stroke-width="3"/></svg>Performance management</li>
      <li><svg viewBox="0 0 20 20"><rect x="1.5" y="4" width="14" height="14" fill="none" stroke="#fff" stroke-width="2"/><path d="M5 10 L9 14 L18 2" fill="none" stroke="#fff" stroke-width="3"/></svg>Coaching</li>
      <li><svg viewBox="0 0 20 20"><rect x="1.5" y="4" width="14" height="14" fill="none" stroke="#fff" stroke-width="2"/><path d="M5 10 L9 14 L18 2" fill="none" stroke="#fff" stroke-width="3"/></svg>Meditation</li>
      <li><svg viewBox="0 0 20 20"><rect x="1.5" y="4" width="14" height="14" fill="none" stroke="#fff" stroke-width="2"/><path d="M5 10 L9 14 L18 2" fill="none" stroke="#fff" stroke-width="3"/></svg>Den feminina essensen</li>
    </ul>

    <h3 class="about-title">ABOUT US</h3>
    <div class="about-rule"></div>
    <p class="about-text">Vi har blivit duktiga på att prestera på bekostnad av kontakten med vår kropp och själ, när vi egentligen behöver raka motsatsen. Ett holistiskt ledarskap av människor som har en god självkännedom, som växer i utmaningarna, människor som vet att sårbarhet ger en ojämförbar styrka och inte underskattar sitt briljanta intellekt. Världen behöver människor som lever och leder från en helt ny plats. Det visa feminina kan leda oss dit.</p>

    <div class="footer"><span class="footer-dot"></span>www.brightmeadow.se</div>
  </div>
</div>
</body>
</html>
```